I have a business that exists already (Linden Conservatory of Music) that we offer music lessons to all instruments. I recently opened a smaller version called CHORDS by Linden that will only teach piano lessons. What I'm looking for now is a 3 page Website on word press. After I choose the design I like I want to be able to take over the website and bring it to our hosting company. We want full control of it and our team will take over. The reason I'm doing this is to have other visions and ideas from others. The first page will be about the company and our message/vision. Second page about the piano lessons. The third will be about franchising this concept "Chords by Linden" Attached are 3 Logos . Please refer to our existing website www.lindenmusicconservatory.example to look at our piano page and franchising page. Please feel free to message me if you need more info. Thanks
Please note I do not want the new website (Chords by Linden) To look like the other Website (Linden Conservatory of Music) Fresh new look. I do not want the colours red or using the Red logo. I only provided it so that you have an Idea of What the other business looks like and that you can take the piano content and franchise content off of it. Chords by Linden is smaller concept and only piano lessons.
Thanks
Only Piano lessons for all students
3 page

```html
<!DOCTYPE html>
<html lang="en">
<head>
<meta charset="utf-8">
<title>CHORDS by Linden — Piano Lessons</title>
<link href="https://fonts.googleapis.com/css2?family=Cinzel:wght@400;500&family=Source+Serif+4:ital,opsz,wght@0,8..60,400;1,8..60,400&family=Montserrat:wght@400;500&display=swap" rel="stylesheet">
<style>
:root{
  --blue:#1f9ff1;
  --gold:#e4c35b;
  --gold-band:#eac866;
  --ink:#1d1d1d;
  --body:#333;
  --panel:#f2f2f2;
  --dark:#474747;
  --white:#fff;
}
*{box-sizing:border-box;margin:0;padding:0}
html,body{width:1200px;height:3176px;overflow:hidden;background:var(--white)}
body{position:relative;font-family:"Source Serif 4",Georgia,serif;color:var(--body)}
.abs{position:absolute}
.head-serif{font-family:"Cinzel",serif;color:var(--ink);font-weight:400}
.btn{display:inline-flex;align-items:center;justify-content:center;font-family:"Cinzel",serif;color:var(--white);background:var(--blue);font-size:16px;letter-spacing:.5px;text-decoration:none}
.btn.pos{position:absolute}
.btn.gold{background:var(--gold);color:#3a2e0a;font-size:12px;font-weight:500}
.rule{position:absolute;height:2px;width:34px;background:var(--blue)}
.rule.gold{background:var(--gold)}
p.copy{font-size:14px;line-height:25.5px}

/* header */
.site-header{position:absolute;left:0;top:0;width:1200px;height:92px}
.brand{left:142px;top:24px;font-family:"Cinzel",serif;font-size:28px;color:var(--ink);display:flex;align-items:center;gap:8px}
.brand-mark{width:14px;height:14px;background:var(--ink)}
.main-nav{top:38px;left:0;width:1200px;font-family:"Cinzel",serif;font-size:13.5px;letter-spacing:.8px;color:#222}
.main-nav span{position:absolute;white-space:nowrap}
.main-nav .active{color:var(--blue)}

/* hero */
.hero{left:0;top:92px;width:1200px;height:481px;background:linear-gradient(90deg,#3b2f25 0%,#7b6a58 14%,#d9c7ae 30%,#eadac2 55%,#f1e4cd 80%,#ecdcc2 100%)}
.hero-text{right:144px;top:220px;text-align:right;font-family:"Cinzel",serif;color:#1c1c1c}
.hero-text .l1{font-size:31px;line-height:48px}
.hero-text .l2{font-size:48px;line-height:54px}
.hero-text .l3{font-size:31px;line-height:48px}

/* about */
.about-title{left:0;width:1200px;top:646px;text-align:center;font-size:31px}
.about-sub{left:0;width:1200px;top:706px;text-align:center;font-style:italic;font-size:22px;color:#222;font-weight:400}
.about-copy{left:160px;width:880px;top:744px;text-align:center}
.about-copy p+p{margin-top:9px}
.about-copy .btn{margin-top:16px;width:155px;height:34px}

/* vision */
.vision-photo{left:0;top:997px;width:596px;height:544px;background:linear-gradient(135deg,#c9c6c0 0%,#8b7b6d 35%,#e9e8e6 65%,#f5f5f5 100%)}
.vision-panel{left:596px;top:997px;width:604px;height:544px;background:var(--panel)}
.blue-bar{position:absolute;width:7px;background:var(--blue)}
.vision-title{left:635px;top:1116px;font-size:33px;letter-spacing:.5px}
.vision-copy{left:635px;top:1182px;width:425px}
.vision-copy p+p{margin-top:6px}
.vision-copy .btn{margin-top:14px;margin-left:2px;width:183px;height:33px}

/* programs */
.prog-title{left:143px;top:1668px;font-size:25px;line-height:36px}
.prog-block{left:143px;top:1763px;width:440px}
.prog-list{list-style:none;font-size:14px;line-height:25.5px}
.prog-list li{position:relative;padding-left:25px;margin-bottom:7px}
.prog-list svg{position:absolute;left:0;top:6px}
.prog-block .btn{margin-top:6px;margin-left:-1px;width:182px;height:34px}
.prog-photo{left:604px;top:1619px;width:596px;height:544px;background:linear-gradient(135deg,#4a4440 0%,#8a6e58 40%,#c39a7a 65%,#3d3835 100%)}

/* franchise */
.franchise{left:0;top:2235px;width:1200px;height:268px;background:linear-gradient(180deg,#e9e9e9,#f4f4f4 40%,#efefef)}
.fr-title{left:0;width:1200px;top:2296px;text-align:center;font-size:33px}
.fr-sub{left:0;width:1200px;top:2358px;text-align:center;font-family:"Montserrat",sans-serif;font-size:15px;letter-spacing:.6px;color:#333}

/* booking */
.book-top{left:0;top:2503px;width:1200px;height:181px;background:linear-gradient(180deg,#0f0f0f,#2b2b2b 70%,#3a3a3a)}
.book-base{left:0;top:2684px;width:1200px;height:297px;background:var(--dark)}
.book-title{left:0;width:1200px;top:2568px;text-align:center;font-size:27px;color:var(--white)}
.form-card{left:142px;top:2641px;width:916px;height:270px;background:var(--white)}
.field{position:absolute;background:var(--white);box-shadow:0 1px 6px rgba(0,0,0,.14);font-family:"Montserrat",sans-serif;font-size:11.5px;color:#666;padding:12px 14px;letter-spacing:.3px}

/* footer */
.contact-band{left:0;top:2981px;width:1200px;height:195px;background:var(--gold-band)}
.contact-col{position:absolute;top:3030px;width:320px;margin-left:-160px;text-align:center}
.contact-icon{height:50px;display:flex;align-items:flex-end;justify-content:center;margin-bottom:10px}
.contact-col .label{font-family:"Source Serif 4",serif;font-size:14px;letter-spacing:.5px;color:#1a1a1a}
.contact-col .val{font-family:"Montserrat",sans-serif;font-size:12.5px;line-height:21px;color:#1a1a1a}
</style>
</head>
<body>

<header class="site-header">
  <div class="abs brand"><span class="brand-mark"></span>CHORDS by Linden</div>
  <nav class="abs main-nav">
    <span class="active" style="left:596px">HOME</span>
    <span style="left:675px">PIANO LESSONS</span>
    <span style="left:825px">FRANCHISING</span>
    <span style="left:963px">CONTACT US</span>
  </nav>
</header>

<section>
  <div class="abs hero" role="img" aria-label="Smiling young girl playing a black upright piano in a bright room"></div>
  <div class="abs hero-text">
    <div class="l1">We Will Provide</div>
    <div class="l2">Piano Lessons</div>
    <div class="l3">For All Students</div>
  </div>
  <a class="btn pos" style="left:875px;top:383px;width:183px;height:35px">Contact Us Today</a>
</section>

<section>
  <h2 class="abs head-serif about-title">ABOUT CHORDS by Linden</h2>
  <div class="rule" style="left:583px;top:690px"></div>
  <h3 class="abs about-sub">Playing the Piano</h3>
  <div class="abs about-copy">
    <p class="copy">When you think of a piano, you probably envision black and white keys but the piano is more than those harmonious sounds created by the player. The versatility and the musicianship instilled into the player&nbsp; from those keys is the true magic that comes from playing piano!</p>
    <p class="copy">Starting from the grassroots, experience different methods and styles of playing piano. To mark the milestones of progression, engage in one of Linden’s many unique performance opportunities like annual festival competitions, recitals or our examinations (Linden &amp; NMB). Penultimately, at the end of the journey, join our elite teaching program to bring the same joy of learning the piano to another student.</p>
    <a class="btn">Read More</a>
  </div>
</section>

<section>
  <div class="abs vision-photo" role="img" aria-label="Teacher and boy seated together at a white grand piano"></div>
  <div class="abs vision-panel"></div>
  <div class="blue-bar" style="left:596px;top:1094px;height:351px"></div>
  <h2 class="abs head-serif vision-title">OUR VISION</h2>
  <div class="rule" style="left:635px;top:1171px"></div>
  <div class="abs vision-copy">
    <p class="copy">Our Mission is Lorem ipsum dolor sit amet, consectetuer adipiscig elit, sed diama nonummy nibh euismod tincidunt ut laoreet dolore magna aliquam erat volutpat. Ut wisi enim ad minim veniam.</p>
    <p class="copy">Lorem hendrerit in vulputate velit esse molestie consequat, velocity illum dolore eu feugiat nulla facilisis at vero eros et accumsan etlict iusto odio dignissim qui blandit praesent luptatum zzril delenit loei augue duis dolore te feugait nulla facilisi.</p>
    <a class="btn">Contact Us Today</a>
  </div>
</section>

<section>
  <h2 class="abs head-serif prog-title">OUR PROGRAMS ALSO PROVIDE<br>STUDENTS THE OPPORTUNITY TO:</h2>
  <div class="rule" style="left:143px;top:1751px"></div>
  <div class="abs prog-block">
    <ul class="prog-list">
      <li><svg width="15" height="12" viewBox="0 0 15 12"><path d="M1 5h3v6H1zM4 5l3-4h1l-1 4h6a1 1 0 010 2h-1v2a1 1 0 01-1 1H4" fill="none" stroke="#1f9ff1" stroke-width="1.3"/></svg>Participate in large-scale performances.</li>
      <li><svg width="15" height="12" viewBox="0 0 15 12"><path d="M1 5h3v6H1zM4 5l3-4h1l-1 4h6a1 1 0 010 2h-1v2a1 1 0 01-1 1H4" fill="none" stroke="#1f9ff1" stroke-width="1.3"/></svg>Perform at Linden’s many community events on a regular basis.</li>
      <li><svg width="15" height="12" viewBox="0 0 15 12"><path d="M1 5h3v6H1zM4 5l3-4h1l-1 4h6a1 1 0 010 2h-1v2a1 1 0 01-1 1H4" fill="none" stroke="#1f9ff1" stroke-width="1.3"/></svg>Access the GTA’s coolest Broadcast stage</li>
      <li><svg width="15" height="12" viewBox="0 0 15 12"><path d="M1 5h3v6H1zM4 5l3-4h1l-1 4h6a1 1 0 010 2h-1v2a1 1 0 01-1 1H4" fill="none" stroke="#1f9ff1" stroke-width="1.3"/></svg>Attend Clinics, Masterclasses, and Jam Nights</li>
      <li><svg width="15" height="12" viewBox="0 0 15 12"><path d="M1 5h3v6H1zM4 5l3-4h1l-1 4h6a1 1 0 010 2h-1v2a1 1 0 01-1 1H4" fill="none" stroke="#1f9ff1" stroke-width="1.3"/></svg>Access the Linden Rocks band program. Linden’s Band Program empowers and electrifies students to come together, create music and confidently hit the stage with their own band identity while having fun and honing their instrument.</li>
      <li><svg width="15" height="12" viewBox="0 0 15 12"><path d="M1 5h3v6H1zM4 5l3-4h1l-1 4h6a1 1 0 010 2h-1v2a1 1 0 01-1 1H4" fill="none" stroke="#1f9ff1" stroke-width="1.3"/></svg>Register in our elite teaching program to learn how to pass on the magic and passion of playing the piano to students.</li>
    </ul>
    <a class="btn">Contact Us Today</a>
  </div>
  <div class="blue-bar" style="left:597px;top:1714px;height:352px"></div>
  <div class="abs prog-photo" role="img" aria-label="Girl in a polka-dot top playing a keyboard beside her teacher, with a student ensemble behind"></div>
</section>

<section>
  <div class="abs franchise" role="img" aria-label="Faded close-up of hands on piano keys"></div>
  <h2 class="abs head-serif fr-title">FRANCHISE OPPORTUNITIES</h2>
  <div class="rule gold" style="left:583px;top:2346px"></div>
  <p class="abs fr-sub">Be Part Of The Linden Conservatory Family</p>
  <a class="btn gold pos" style="left:543px;top:2399px;width:114px;height:34px">READ MORE</a>
</section>

<section>
  <div class="abs book-top" role="img" aria-label="Dark close-up of piano keys"></div>
  <div class="abs book-base"></div>
  <h2 class="abs head-serif book-title">BOOK A MEETING WITH US</h2>
  <div class="rule gold" style="left:583px;top:2607px"></div>
  <form class="abs form-card">
    <div class="field" style="left:47px;top:33px;width:267px;height:36px">Your Name*</div>
    <div class="field" style="left:324px;top:33px;width:268px;height:36px">Your Phone*</div>
    <div class="field" style="left:604px;top:33px;width:268px;height:36px">Your Email*</div>
    <div class="field" style="left:47px;top:86px;width:825px;height:87px">Your Message*</div>
    <a class="btn gold pos" style="left:401px;top:200px;width:114px;height:33px">SUBMIT</a>
  </form>
</section>

<footer class="abs contact-band"></footer>
<div class="contact-col" style="left:256px">
  <div class="contact-icon"><svg width="42" height="40" viewBox="0 0 42 40"><path d="M9 6c-3 2-4 6-2 11 3 7 9 14 17 18 4 2 8 1 10-2l1-2-6-5-3 2c-1 1-3 1-4 0-3-2-6-6-8-9-1-1-1-3 0-4l3-2-4-7z" fill="#111"/><path d="M24 4a13 13 0 0113 13M24 9a8 8 0 018 8M24 14a3 3 0 013 3" fill="none" stroke="#111" stroke-width="2.4" stroke-linecap="round"/></svg></div>
  <div class="label">CALL US</div>
  <div class="val">1-800-555-0142</div>
</div>
<div class="contact-col" style="left:599px">
  <div class="contact-icon"><svg width="34" height="48" viewBox="0 0 34 48"><path d="M17 2C9 2 3 8 3 16c0 10 14 30 14 30s14-20 14-30C31 8 25 2 17 2z" fill="#111"/><circle cx="17" cy="16" r="6" fill="#eac866"/></svg></div>
  <div class="label">POSTAL ADDRESS</div>
  <div class="val">48 Maple Row, Suite 210<br>Northbrook, ON A1B 2C3</div>
</div>
<div class="contact-col" style="left:910px">
  <div class="contact-icon"><svg width="46" height="36" viewBox="0 0 46 36"><rect x="1" y="4" width="44" height="30" rx="3" fill="#111"/><path d="M3 7l20 14 20-14" fill="none" stroke="#eac866" stroke-width="2.4"/></svg></div>
  <div class="label">E-MAIL</div>
  <div class="val">info@chordsbylinden.example</div>
</div>

</body>
</html>
```